Desktop and Networking Support Course 9.17.25

Important the ad should not be very busy with the text taking up the major part of the ad .. please do not make the text so big that it takes up most of the ad..
Flyer Design Brief for Graphic Artist
also i am looking for something unique or creative that it will stand out .
Size & Layout:
Full Page with Bleed: 8” x 10.75” + 0.25” bleed on all sides.
Footer Space: Leave a 1-inch margin at the bottom for footer content (e.g., contact info, logo, or call-to-action).
Target Audience:
College-age students (around 24 years old)
Located in the USA
Interested in creative, professional, and career-building opportunities
Purpose:
To attract students to enroll in a college program
Flyer should be eye-catching, unique, and creative
Text must be clear and readable,
Design Style:
Use vector art, typography, or photography — your choice
If using photography, feature a white young professional USA citizen:
Wearing a white collared shirt
not with long hair
Creative Direction:
The flyer should stand out visually — something people would want to look at and keep
Showcase creativity and professionalism
Use bold colors, dynamic layout, or unexpected design elements to grab attention
Avoid clutter — keep the design balanced and clean
Text Suggestions (can be adjusted):
Footer,
please leave one inch on the bottom for the footer

```html
<!DOCTYPE html>
<html lang="en">
<head>
<meta charset="UTF-8">
<title>Desktop &amp; Network Support Course</title>
<link rel="stylesheet" href="https://fonts.googleapis.com/css2?family=Poppins:ital,wght@0,400;0,600;0,700;0,800;1,400&family=Great+Vibes&display=swap">
<style>
  :root{
    --navy-deep:#050838;
    --navy:#0a1260;
    --royal:#0b1fd8;
    --sky:#1aa6ff;
    --gold:#e9be1c;
    --gold-deep:#d9a30a;
    --gold-dark:#b8900c;
    --ink:#0a0d45;
    --white:#ffffff;
    --footer:#ffffff;
    --shirt:#e4e7ee;
    --shirt-shade:#c3c8d3;
    --trouser:#15171d;
  }
  *{margin:0;padding:0;box-sizing:border-box}
  html,body{width:946px;height:1200px;overflow:hidden;background:var(--footer)}
  body{font-family:'Poppins',sans-serif;position:relative}
  .flyer{position:absolute;left:0;top:0;width:946px;height:1200px;overflow:hidden;background:var(--footer)}
  .hero{
    position:absolute;left:0;top:0;width:946px;height:1094px;overflow:hidden;
    background:
      radial-gradient(ellipse 420px 320px at 100% 0%, rgba(20,40,240,.95), transparent 70%),
      radial-gradient(ellipse 360px 260px at 0% 100%, rgba(20,110,230,.55), transparent 70%),
      linear-gradient(170deg, var(--navy-deep) 0%, var(--navy) 55%, #0d1a8a 100%);
  }
  .portrait{
    position:absolute;left:600px;top:170px;width:346px;height:924px;z-index:3;
    border-radius:170px 0 0 0;
    background:linear-gradient(180deg, var(--shirt-shade) 0%, var(--shirt) 35%, var(--shirt) 78%, #5a5e68 84%, var(--trouser) 90%, var(--trouser) 100%);
    -webkit-mask-image:linear-gradient(90deg, transparent 0%, #000 14%);
            mask-image:linear-gradient(90deg, transparent 0%, #000 14%);
  }
  .title-script{position:absolute;left:112px;top:34px;font-family:'Great Vibes',cursive;font-size:92px;color:var(--white);line-height:1;z-index:2}
  .title-line{position:absolute;left:72px;font-weight:700;color:var(--white);font-size:90px;line-height:1;letter-spacing:-1px;z-index:1}
  .title-line.career{top:106px}
  .title-line.click{top:180px}
  .title-tag{
    position:absolute;left:406px;top:127px;width:185px;height:46px;
    background:linear-gradient(90deg,#1a8fe8,#2cb2f5);
    color:var(--ink);font-weight:800;font-size:33px;line-height:46px;text-align:center;
  }
  .course-band{position:absolute;left:74px;top:301px;width:660px;height:135px;z-index:2}
  .course-band svg{position:absolute;inset:0}
  .course-band h1{position:absolute;left:32px;top:14px;font-weight:700;font-size:47px;line-height:52px;color:var(--ink);letter-spacing:.2px}
  .stat{position:absolute;left:78px;top:474px;display:flex;align-items:center;gap:12px}
  .stat-number{font-weight:800;font-size:72px;color:var(--sky);line-height:1;letter-spacing:-2px}
  .stat-label{font-weight:600;font-size:29px;line-height:33px;color:var(--white)}
  .class-bar{
    position:absolute;left:76px;top:558px;width:440px;height:38px;
    background:var(--gold-deep);color:var(--ink);
    font-weight:700;font-size:30px;line-height:38px;letter-spacing:4.5px;padding-left:45px;
  }
  .ranking{position:absolute;left:75px;top:635px;color:var(--white)}
  .ranking p{font-weight:600;font-size:20px}
  .ranking p span{color:var(--sky)}
  .ranking cite{display:block;font-style:italic;font-size:17px;margin-top:4px}
  .features{position:absolute;left:77px;top:738px;width:540px;list-style:none;z-index:2}
  .feature{
    height:74px;margin-bottom:10px;border:1px solid #2a6cff;border-radius:16px;
    background:linear-gradient(90deg,#0c1a8c,#1a2ec0);
    display:flex;align-items:center;padding-left:18px;gap:24px;
    color:var(--white);font-size:23px;line-height:28px;
  }
  .feature svg{flex:none}
  .perks{position:absolute;left:81px;top:1034px;width:787px;height:60px;display:flex;z-index:4}
  .perk{color:var(--white);font-size:23px;line-height:60px;border-radius:12px 12px 0 0}
  .perk.mode{width:420px;background:var(--gold-deep);padding-left:26px;z-index:1}
  .perk.aid{flex:1;background:var(--gold-dark);margin-left:-10px;padding-left:22px}
</style>
</head>
<body>
<main class="flyer">
  <section class="hero">
    <div class="title-script">Your</div>
    <div class="title-line career">Career</div>
    <div class="title-tag">IS JUST A</div>
    <div class="title-line click">Click Away</div>

    <div class="course-band">
      <svg width="660" height="135" viewBox="0 0 660 135" aria-hidden="true">
        <defs><linearGradient id="bandGold" x1="0" x2="1"><stop offset="0" stop-color="#f0cc2a"/><stop offset="1" stop-color="#dca40a"/></linearGradient></defs>
        <path d="M0 0 H660 C610 40 560 110 470 135 H70 C30 135 0 105 0 70 Z" fill="url(#bandGold)"/>
      </svg>
      <h1>DESKTOP &amp; NETWORK<br>SUPPORT COURSE</h1>
    </div>

    <div class="stat">
      <span class="stat-number">90%</span>
      <span class="stat-label">EMPLOYMENT<br>RATE</span>
    </div>
    <div class="class-bar">CLASS OF 2024</div>

    <div class="ranking">
      <p>Prepare for 3 of the <span>Top 10 Tech Jobs</span></p>
      <cite>National Career Review 2025</cite>
    </div>

    <ul class="features">
      <li class="feature"><svg width="24" height="24" viewBox="0 0 24 24" aria-hidden="true"><circle cx="12" cy="12" r="12" fill="#22c7ff"/><path d="M6.5 12.5l3.5 3.5 7-7.5" stroke="#0a1260" stroke-width="2.6" fill="none" stroke-linecap="round" stroke-linejoin="round"/></svg><span>Hands-On Desktop &amp;<br>Network Training</span></li>
      <li class="feature"><svg width="24" height="24" viewBox="0 0 24 24" aria-hidden="true"><circle cx="12" cy="12" r="12" fill="#22c7ff"/><path d="M6.5 12.5l3.5 3.5 7-7.5" stroke="#0a1260" stroke-width="2.6" fill="none" stroke-linecap="round" stroke-linejoin="round"/></svg><span>Real-World Troubleshooting Skills</span></li>
      <li class="feature"><svg width="24" height="24" viewBox="0 0 24 24" aria-hidden="true"><circle cx="12" cy="12" r="12" fill="#22c7ff"/><path d="M6.5 12.5l3.5 3.5 7-7.5" stroke="#0a1260" stroke-width="2.6" fill="none" stroke-linecap="round" stroke-linejoin="round"/></svg><span>Ready for IT Jobs</span></li>
    </ul>

    <div class="portrait" role="img" aria-label="Photo of a smiling young professional in a white collared shirt with arms crossed"></div>

    <div class="perks">
      <div class="perk mode">In-Person and Remote Options</div>
      <div class="perk aid">Partial Scholarships Offered</div>
    </div>
  </section>
</main>
</body>
</html>
```